KRT Flyer to attract applicants 11x17

Lantern Stagehand Collective provides crew for local concerts, filming, theater, and corporate events.
The flyer will be posted on bulletin boards at colleges with theater programs.
Our primary venues are historic theaters in downtown LA
Need a 11x17 poster to attract potential applicants/crew
I have attached a poster that one of our staff made that has all if the relevant info - but i know the poster can look much better than that. I have also attached many images and our logo. It is not necessary to use all of the images, or any of them. The two images of the theater interiors are the venues we operate so they would be the first to include. I can send additional info or images upon request. Thank you

Industry/Entity Type

Entertainment

Requirements
Must have
• APPLY@KRTCREW.EXAMPLE

```html
<!DOCTYPE html>
<html lang="en">
<head>
<meta charset="utf-8">
<title>KRT Crew Recruitment Flyer</title>
<link rel="stylesheet" href="https://fonts.googleapis.com/css2?family=Poppins:wght@300;400;500&display=swap">
<style>
  :root {
    --page: #ffffff;
    --plum-deep: #1f0a26;
    --plum: #34123d;
    --plum-light: #4a1b52;
    --white: #ffffff;
    --text-soft: #e9dff0;
    --orange: #f7941d;
    --red: #e5232e;
    --violet: #8a2f9a;
    --gold: #ffc23d;
  }
  * { margin: 0; padding: 0; box-sizing: border-box; }
  html, body {
    width: 813px; height: 1200px; overflow: hidden;
    background: var(--page);
    font-family: "Poppins", sans-serif;
  }
  .flyer {
    position: absolute; left: 72px; top: 68px;
    width: 670px; height: 1052px;
    background: radial-gradient(ellipse at 50% 45%, var(--plum-light) 0%, var(--plum) 45%, var(--plum-deep) 100%);
    color: var(--white);
    overflow: hidden;
  }
  .brand {
    position: absolute; top: 40px; left: 0; width: 100%;
    display: flex; flex-direction: column; align-items: center; gap: 12px;
  }
  .brand-dot {
    width: 54px; height: 54px; border-radius: 50%;
    border: 3px solid var(--white);
  }
  .brand-name {
    font-size: 15px; font-weight: 500; letter-spacing: 2px;
    text-transform: uppercase; color: var(--white);
  }
  .header-arc { position: absolute; top: 150px; left: 0; width: 670px; height: 60px; }
  .headline {
    position: absolute; top: 196px; width: 100%; text-align: center;
    font-size: 38px; font-weight: 400;
  }
  .dots {
    position: absolute; top: 254px; width: 100%;
    display: flex; justify-content: center; gap: 9px;
  }
  .dots span { width: 8px; height: 8px; border-radius: 50%; }
  .dots .dot-orange { background: var(--orange); }
  .dots .dot-red { background: var(--red); }
  .dots .dot-violet { background: var(--violet); }
  .intro {
    position: absolute; top: 276px; width: 100%; text-align: center;
    font-size: 15px; font-weight: 300; line-height: 1.5; color: var(--text-soft);
  }
  .venue-circle { position: absolute; left: 55px; top: 360px; width: 560px; height: 560px; }
  .apply-label {
    position: absolute; top: 930px; width: 100%; text-align: center;
    font-size: 16px; font-weight: 400;
  }
  .apply-email {
    position: absolute; top: 952px; width: 100%; text-align: center;
    font-size: 30px; font-weight: 400; letter-spacing: 0.5px;
  }
  .tagline {
    position: absolute; top: 1010px; width: 100%; text-align: center;
    font-size: 14px; font-weight: 400; color: var(--text-soft);
  }
</style>
</head>
<body>
<main class="flyer">
  <header class="brand">
    <span class="brand-dot"></span>
    <span class="brand-name">Lantern Stagehand Collective</span>
  </header>

  <svg class="header-arc" viewBox="0 0 670 60" aria-hidden="true">
    <defs>
      <linearGradient id="arcGrad" x1="0" x2="1">
        <stop offset="0" stop-color="#4a1b52"/>
        <stop offset="0.25" stop-color="#e5232e"/>
        <stop offset="0.5" stop-color="#f7941d"/>
        <stop offset="0.75" stop-color="#e5232e"/>
        <stop offset="1" stop-color="#4a1b52"/>
      </linearGradient>
    </defs>
    <path d="M0 55 Q335 -5 670 55" fill="none" stroke="url(#arcGrad)" stroke-width="6"/>
  </svg>

  <h1 class="headline">Has Open Positions</h1>
  <div class="dots"><span class="dot-orange"></span><span class="dot-red"></span><span class="dot-violet"></span></div>
  <p class="intro">We are looking for talented technicians<br>to add to our roster of skilled professionals.</p>

  <svg class="venue-circle" viewBox="0 0 560 560">
    <defs>
      <clipPath id="innerCircle"><circle cx="280" cy="280" r="212"/></clipPath>
      <linearGradient id="ringGrad" x1="0" y1="0" x2="1" y2="1">
        <stop offset="0" stop-color="#ffc23d"/>
        <stop offset="0.45" stop-color="#f7941d"/>
        <stop offset="1" stop-color="#e5232e"/>
      </linearGradient>
      <linearGradient id="cityGrad" x1="0" y1="0" x2="0" y2="1">
        <stop offset="0" stop-color="#1a2a5c"/>
        <stop offset="1" stop-color="#3d6fb5"/>
      </linearGradient>
      <radialGradient id="stageGrad" cx="0.4" cy="0.3" r="0.8">
        <stop offset="0" stop-color="#e8ecf5"/>
        <stop offset="0.4" stop-color="#4a5b8c"/>
        <stop offset="1" stop-color="#101828"/>
      </radialGradient>
      <radialGradient id="theaterGrad" cx="0.6" cy="0.5" r="0.8">
        <stop offset="0" stop-color="#f2b84a"/>
        <stop offset="0.5" stop-color="#a14a1c"/>
        <stop offset="1" stop-color="#3a1410"/>
      </radialGradient>
      <linearGradient id="concertGrad" x1="0" y1="0" x2="1" y2="1">
        <stop offset="0" stop-color="#6a3fb0"/>
        <stop offset="1" stop-color="#22124a"/>
      </linearGradient>
    </defs>

    <circle cx="280" cy="280" r="262" fill="none" stroke="url(#ringGrad)" stroke-width="9"
            stroke-dasharray="1100 546" transform="rotate(-200 280 280)"/>
    <circle cx="280" cy="280" r="262" fill="none" stroke="#8a2f9a" stroke-width="4"
            stroke-dasharray="300 1346" transform="rotate(40 280 280)"/>
    <circle cx="280" cy="280" r="232" fill="none" stroke="url(#ringGrad)" stroke-width="4"
            stroke-dasharray="900 558" transform="rotate(30 280 280)"/>

    <g clip-path="url(#innerCircle)">
      <rect x="60" y="60" width="220" height="220" fill="url(#cityGrad)" role="img" aria-label="Photo of the downtown city skyline at night"/>
      <rect x="280" y="60" width="220" height="220" fill="url(#stageGrad)" role="img" aria-label="Photo of a performer on a lit stage"/>
      <rect x="60" y="280" width="220" height="220" fill="url(#theaterGrad)" role="img" aria-label="Photo of a historic theater interior"/>
      <rect x="280" y="280" width="220" height="220" fill="url(#concertGrad)" role="img" aria-label="Photo of a concert hall with stage lighting"/>
      <rect x="275" y="60" width="10" height="440" fill="#34123d"/>
      <rect x="60" y="275" width="440" height="10" fill="#34123d"/>
    </g>
  </svg>

  <p class="apply-label">Send Resume to</p>
  <p class="apply-email">APPLY@KRTCREW.EXAMPLE</p>
  <p class="tagline">We provides crew for local concerts, filming, theater, and corporate events</p>
</main>
</body>
</html>
```